Vantro cards

I am in the auto motive, transportation business I would like a business card that is Something cool, modern edgy, having to do with car culture. I offer towing service for high and exotic cars. I also provide towing for collisions and car accidents. I offer open and enclosed transport nationwide.

Target Market(s)

Car culture people high end auto collectors

Industry/Entity Type

Towing car carrier

Contact Information for Business Card

My company colors black yellow and silver

Font styles to use
Serif

```html
<!DOCTYPE html>
<html lang="en">
<head>
<meta charset="utf-8">
<title>Vantro Transportation — Business Card</title>
<link rel="stylesheet" href="https://fonts.googleapis.com/css2?family=Poppins:wght@400;500;600;700&display=swap">
<style>
  :root {
    --stage: #e9e7e2;
    --ink: #0b0b0b;
    --paper: #ffffff;
    --yellow: #fbe05c;
    --yellow-deep: #f4cf2a;
    --pattern-black: #111111;
    --text-dark: #141414;
  }
  * { box-sizing: border-box; margin: 0; padding: 0; }
  html, body {
    width: 1200px;
    height: 900px;
    overflow: hidden;
    background: var(--stage);
    font-family: "Poppins", sans-serif;
  }
  .stage {
    position: relative;
    width: 1200px;
    height: 900px;
  }
  .card {
    position: absolute;
    left: 250px;
    width: 700px;
    height: 400px;
    overflow: hidden;
    box-shadow: 0 10px 28px rgba(0, 0, 0, 0.18);
  }

  /* Back of card */
  .card-back {
    top: 40px;
    background: var(--ink);
  }
  .card-back .pattern-field {
    position: absolute;
    inset: 0;
    background: var(--pattern-black);
  }
  .card-back .back-wordmark {
    position: absolute;
    left: 470px;
    top: 200px;
    font-weight: 700;
    font-size: 34px;
    letter-spacing: 2px;
    color: var(--yellow);
    text-transform: uppercase;
  }

  /* Front of card */
  .card-front {
    top: 470px;
    background: var(--paper);
  }
  .card-front .wave {
    position: absolute;
    inset: 0;
    width: 700px;
    height: 400px;
  }
  .wave .wave-yellow { fill: var(--yellow); }
  .wave .wave-black { fill: var(--ink); }

  .identity {
    position: absolute;
    left: 48px;
    top: 70px;
  }
  .identity .person-name {
    font-weight: 600;
    font-size: 28px;
    letter-spacing: 1px;
    color: var(--yellow-deep);
    text-transform: uppercase;
    line-height: 1.1;
  }
  .identity .person-role {
    font-weight: 400;
    font-size: 19px;
    color: var(--text-dark);
    margin-top: 2px;
  }

  .contact {
    position: absolute;
    left: 48px;
    top: 170px;
    list-style: none;
    font-size: 19px;
    color: var(--text-dark);
    line-height: 1.35;
  }
  .contact li {
    display: flex;
    align-items: center;
    gap: 12px;
  }
  .contact .icon {
    width: 24px;
    height: 24px;
    flex: none;
  }
  .contact .icon path { fill: var(--yellow-deep); }
  .contact .address {
    margin-top: 14px;
    padding-left: 36px;
    display: block;
  }

  .brand-wordmark {
    position: absolute;
    right: 56px;
    top: 95px;
    font-weight: 700;
    font-size: 52px;
    letter-spacing: 3px;
    color: var(--ink);
    text-transform: uppercase;
  }

  .website {
    position: absolute;
    right: 40px;
    bottom: 98px;
    font-size: 18px;
    font-weight: 500;
    color: var(--paper);
  }
</style>
</head>
<body>
<main class="stage">

  <section class="card card-back" aria-label="Card back">
    <div class="pattern-field" role="img" aria-label="Repeating faint company marks tiled across a black background"></div>
    <span class="back-wordmark">Vantro</span>
  </section>

  <section class="card card-front" aria-label="Card front">
    <svg class="wave" viewBox="0 0 700 400" aria-hidden="true">
      <path class="wave-yellow" d="M0,318 C230,330 430,290 560,215 C610,188 660,170 700,160 L700,400 L0,400 Z"/>
      <path class="wave-black" d="M0,343 C250,352 450,315 580,245 C625,222 665,205 700,196 L700,400 L0,400 Z"/>
    </svg>

    <div class="identity">
      <h1 class="person-name">Marcus Hale</h1>
      <p class="person-role">Managing Director</p>
    </div>

    <ul class="contact">
      <li>
        <svg class="icon" viewBox="0 0 24 24" aria-hidden="true">
          <path d="M6.6 10.8a15.1 15.1 0 0 0 6.6 6.6l2.2-2.2a1 1 0 0 1 1-.25 11.4 11.4 0 0 0 3.6.57 1 1 0 0 1 1 1V20a1 1 0 0 1-1 1A17 17 0 0 1 3 4a1 1 0 0 1 1-1h3.5a1 1 0 0 1 1 1c0 1.25.2 2.45.57 3.57a1 1 0 0 1-.25 1z"/>
        </svg>
        <span class="phone">044-987 654 321</span>
      </li>
      <li>
        <svg class="icon" viewBox="0 0 24 24" aria-hidden="true">
          <path d="M2 5h20v14H2z M4 7v.4l8 5.3 8-5.3V7z" fill-rule="evenodd"/>
        </svg>
        <span class="email">hello@vantrotow.com</span>
      </li>
      <li class="address">88 Harbor Road, Unit 4<br>Eastfield, 20731</li>
    </ul>

    <span class="brand-wordmark">Vantro</span>

    <span class="website">www.vantrotow.com</span>
  </section>

</main>
</body>
</html>
```